Quorva - corporate Business Card

We need a good look and innovative business card for a new start up company based in Los Angeles called "Quorva". We are in a payment business, including payment card, app, and ewallet. We are expert in online payment and Card not present (CNP) transaction.
We need an innovative, modern business card.

Our logo font is Aero Matics

Target Market(s)

Startup - Bank - Online Payment - Card Manufacturing

Industry/Entity Type

Startup

Contact Information for Business Card

phone: 555 014 7396 - Address: 4172 Marlowe blvd, Brenmoor, OR 97299

Requirements
Must have
• Message: innovative, professional, expert, high tech, trust, online payment expert, security
Nice to have
• no comment
Should not have
• no Comment

```html
<!DOCTYPE html>
<html lang="en">
<head>
<meta charset="utf-8">
<title>Quorva – Business Card</title>
<link rel="stylesheet" href="https://fonts.googleapis.com/css2?family=Exo+2:wght@500&family=Lato:wght@400;700&display=swap">
<style>
  :root {
    --brand-red: #b41f2e;
    --band-black: #0c0c0c;
    --card-white: #f6f6f6;
    --page-bg: #ececec;
    --text-light: #ffffff;
  }
  * { box-sizing: border-box; margin: 0; padding: 0; }
  html, body {
    width: 1200px; height: 586px; overflow: hidden;
    background: var(--page-bg);
    font-family: "Lato", Arial, sans-serif;
  }
  .canvas { position: relative; width: 1200px; height: 586px; }
  .card {
    position: absolute; top: 129px;
    width: 501px; height: 300px;
    background: var(--card-white);
    overflow: hidden;
  }
  .card--front { left: 61px; }
  .card--back { left: 619px; }
  .card__band { position: absolute; inset: 0; width: 501px; height: 300px; }
  .band-edge { fill: var(--band-black); }
  .band-fill { fill: var(--brand-red); }

  .brand { position: absolute; display: flex; align-items: center; }
  .brand__dot { border-radius: 50%; background: var(--brand-red); flex: none; }
  .brand__name {
    font-family: "Exo 2", "Lato", sans-serif; font-weight: 500;
    color: var(--brand-red); line-height: 1; letter-spacing: 0.01em;
  }
  .card--front .brand { left: 65px; top: 66px; gap: 14px; }
  .card--front .brand__dot { width: 108px; height: 108px; }
  .card--front .brand__name { font-size: 76px; }
  .card--back .brand { left: 143px; top: 35px; gap: 10px; }
  .card--back .brand__dot { width: 60px; height: 60px; }
  .card--back .brand__name { font-size: 48px; }

  .website {
    position: absolute; left: 0; right: 0; top: 268px;
    text-align: center; color: var(--text-light);
    font-size: 13px; letter-spacing: 0.28em;
  }

  .holder {
    position: absolute; right: 292px; top: 186px;
    text-align: right; color: var(--text-light);
  }
  .holder__name { font-weight: 700; font-size: 18px; line-height: 22px; }
  .holder__role { font-size: 11.5px; line-height: 16px; margin-top: 3px; }
  .holder__address { font-weight: 700; font-size: 12.5px; line-height: 17px; margin-top: 10px; }

  .divider {
    position: absolute; left: 236px; top: 175px; width: 1px; height: 108px;
    background: linear-gradient(to bottom, transparent, rgba(255,255,255,.75) 20%, rgba(255,255,255,.75) 80%, transparent);
  }

  .contacts { position: absolute; left: 258px; top: 191px; list-style: none; color: var(--text-light); }
  .contacts__item { display: flex; align-items: center; gap: 8px; height: 18px; margin-bottom: 9.5px; font-size: 12.5px; }
  .contacts__icon { width: 17px; height: 17px; flex: none; }
  .icon-disc { fill: var(--text-light); }
  .icon-glyph { fill: var(--brand-red); }
  .icon-line { fill: none; stroke: var(--text-light); stroke-width: 1.2; }
</style>
</head>
<body>
<main class="canvas">

  <section class="card card--front" aria-label="Card front">
    <svg class="card__band" viewBox="0 0 501 300" aria-hidden="true">
      <path class="band-edge" d="M0 262 Q250 180 501 271 L501 300 L0 300 Z"/>
      <path class="band-fill" d="M0 283 Q250 167 501 296 L501 300 L0 300 Z"/>
    </svg>
    <div class="brand">
      <span class="brand__dot"></span>
      <span class="brand__name">quorva</span>
    </div>
    <p class="website">www.quorvapay.com</p>
  </section>

  <section class="card card--back" aria-label="Card back">
    <svg class="card__band" viewBox="0 0 501 300" aria-hidden="true">
      <path class="band-edge" d="M0 167 Q250 88 501 178 L501 300 L0 300 Z"/>
      <path class="band-fill" d="M0 190 Q250 73 501 201 L501 300 L0 300 Z"/>
    </svg>
    <div class="brand">
      <span class="brand__dot"></span>
      <span class="brand__name">quorva</span>
    </div>

    <div class="holder">
      <p class="holder__name">Marcus Halden</p>
      <p class="holder__role">Owner &amp; Founder</p>
      <p class="holder__address">4172 Marlowe blvd,<br>Brenmoor, OR 97299</p>
    </div>

    <div class="divider"></div>

    <ul class="contacts">
      <li class="contacts__item">
        <svg class="contacts__icon" viewBox="0 0 20 20" aria-hidden="true">
          <circle class="icon-disc" cx="10" cy="10" r="10"/>
          <path class="icon-glyph" d="M4.5 8 Q10 4 15.5 8 L14.5 9.5 L12.5 9 L12.3 7.8 Q10 7 7.7 7.8 L7.5 9 L5.5 9.5 Z M6.5 10.5 H13.5 L14.5 14.5 H5.5 Z"/>
        </svg>
        <span>(555) 014-7396</span>
      </li>
      <li class="contacts__item">
        <svg class="contacts__icon" viewBox="0 0 20 20" aria-hidden="true">
          <circle class="icon-disc" cx="10" cy="10" r="10"/>
          <path class="icon-glyph" d="M7 4.5 H13 V7.5 H7 Z M4.5 8.5 H15.5 V13.5 H13.5 V12 H6.5 V13.5 H4.5 Z M7 12.8 H13 V15.5 H7 Z"/>
        </svg>
        <span>(555) 014-7300</span>
      </li>
      <li class="contacts__item">
        <svg class="contacts__icon" viewBox="0 0 20 20" aria-hidden="true">
          <circle class="icon-disc" cx="10" cy="10" r="10"/>
          <rect class="icon-glyph" x="4.5" y="6.5" width="11" height="7.5"/>
          <path class="icon-line" d="M4.8 6.8 L10 11 L15.2 6.8"/>
        </svg>
        <span>MarcusH@quorvapay.com</span>
      </li>
    </ul>
  </section>

</main>
</body>
</html>
```